TALMORK

The business want a professional looking business card. We have a scetch we will add but want the extra upgrade, and would like more suggestions for variations of our business cards.

```html
<!DOCTYPE html>
<html lang="en">
<head>
<meta charset="utf-8">
<title>Talmork Brekkestad – Business Card</title>
<link rel="stylesheet" href="https://fonts.googleapis.com/css2?family=Cormorant+Garamond:wght@700&family=Montserrat:wght@600&display=swap">
<style>
  :root {
    --backdrop: #212121;
    --gold-pale: #f9f4bd;
    --gold-mid: #c9b072;
    --gold-deep: #a88a42;
    --gold-dark: #946428;
    --ink: #5e3a1a;
    --cream: #f6ecb4;
  }
  * { margin: 0; padding: 0; box-sizing: border-box; }
  html, body {
    width: 850px; height: 1200px; overflow: hidden;
    background: var(--backdrop);
  }
  .sheet { position: relative; width: 850px; height: 1200px; }

  .card {
    position: absolute; left: 134px; width: 582px; height: 377px;
    border-radius: 21px; overflow: hidden;
  }
  .card--front {
    top: 139px;
    background: linear-gradient(90deg, var(--gold-pale) 0%, var(--gold-pale) 18%, var(--gold-mid) 38%, var(--gold-deep) 60%, var(--gold-dark) 100%);
  }
  .card--back {
    top: 630px;
    background: linear-gradient(270deg, var(--gold-pale) 0%, var(--gold-pale) 18%, var(--gold-mid) 38%, var(--gold-deep) 60%, var(--gold-dark) 100%);
  }
  .card__frame { position: absolute; inset: 0; width: 582px; height: 377px; }

  .company {
    position: absolute;
    font-family: "Cormorant Garamond", serif;
    font-weight: 700; font-size: 37px; line-height: 1;
    color: var(--ink); letter-spacing: 0.5px; white-space: nowrap;
  }
  .card--front .company { left: 55px; top: 63px; }
  .card--back .company { left: 0; right: 0; top: 172px; text-align: center; }

  .role, .person, .contact__text {
    position: absolute; font-family: "Montserrat", sans-serif;
    font-weight: 600; color: var(--ink); white-space: nowrap;
  }
  .role { left: 55px; top: 108px; font-size: 24px; }
  .person { left: 55px; top: 134px; font-size: 15.5px; }

  .contacts { position: absolute; left: 55px; top: 237px; list-style: none; }
  .contact { position: relative; height: 27.5px; display: flex; align-items: center; }
  .contact__icon { width: 23px; height: 23px; flex: none; }
  .contact__text { position: static; margin-left: 5px; font-size: 16px; }

  .brand {
    position: absolute; left: 329px; width: 200px; top: 0;
    text-align: center;
  }
  .brand__dot {
    position: absolute; left: 70px; top: 166px; width: 60px; height: 60px;
    border-radius: 50%; background: var(--cream);
  }
  .brand__name {
    position: absolute; left: 0; width: 200px; top: 263px;
    font-family: "Cormorant Garamond", serif; font-weight: 700;
    font-size: 31px; letter-spacing: 9px; padding-left: 9px;
    color: var(--cream); line-height: 1;
  }
  .brand__since {
    position: absolute; left: 0; width: 200px; top: 306px;
    font-family: "Montserrat", sans-serif; font-weight: 600;
    font-size: 9px; letter-spacing: 6px; padding-left: 6px;
    color: var(--gold-pale); opacity: 0.75;
  }
</style>
</head>
<body>
<main class="sheet">

  <section class="card card--front" aria-label="Business card front">
    <svg class="card__frame" viewBox="0 0 582 377" aria-hidden="true">
      <defs>
        <linearGradient id="frameFront" x1="0" x2="1" y1="0" y2="0">
          <stop offset="0" stop-color="#f9f4bd" stop-opacity="0"/>
          <stop offset="0.12" stop-color="#f9f4bd" stop-opacity="0"/>
          <stop offset="0.3" stop-color="#f9f4bd" stop-opacity="1"/>
          <stop offset="1" stop-color="#f9f4bd" stop-opacity="1"/>
        </linearGradient>
      </defs>
      <rect x="33.5" y="34.5" width="515" height="308" rx="24" fill="none" stroke="url(#frameFront)" stroke-width="1"/>
    </svg>

    <h1 class="company">TALMORK BREKKESTAD</h1>
    <p class="role">CEO &amp; Founder</p>
    <p class="person">Anders Mikael Brekkestad</p>

    <ul class="contacts">
      <li class="contact">
        <svg class="contact__icon" viewBox="0 0 24 24" aria-hidden="true">
          <circle cx="12" cy="12" r="12" fill="var(--ink)"/>
          <path d="M8.3 6.5c.4-.3 1-.3 1.3.1l1.4 1.9c.3.4.2.9-.1 1.2l-.9.8c.6 1.3 1.7 2.5 3 3.2l.8-.9c.3-.3.9-.4 1.2-.1l1.9 1.4c.4.3.5.9.1 1.3l-1 1.1c-.6.6-1.5.8-2.3.5-3.3-1.3-5.7-3.7-6.9-7-.3-.8-.1-1.7.5-2.3z" fill="var(--gold-pale)"/>
        </svg>
        <span class="contact__text">004791 555 204</span>
      </li>
      <li class="contact">
        <svg class="contact__icon" viewBox="0 0 24 24" aria-hidden="true">
          <circle cx="12" cy="12" r="12" fill="var(--ink)"/>
          <rect x="6" y="8" width="12" height="8.5" rx="1" fill="none" stroke="var(--gold-pale)" stroke-width="1.3"/>
          <path d="M6.5 8.6 12 13l5.5-4.4M6.5 16l4-3.6M17.5 16l-4-3.6" fill="none" stroke="var(--gold-pale)" stroke-width="1.1"/>
        </svg>
        <span class="contact__text">talmork.llc@mailbox.com</span>
      </li>
      <li class="contact">
        <svg class="contact__icon" viewBox="0 0 24 24" aria-hidden="true">
          <circle cx="12" cy="12" r="12" fill="var(--ink)"/>
          <g fill="none" stroke="var(--gold-pale)" stroke-width="1.1">
            <circle cx="12" cy="12" r="6"/>
            <ellipse cx="12" cy="12" rx="2.6" ry="6"/>
            <path d="M6 12h12M7 9h10M7 15h10"/>
          </g>
        </svg>
        <span class="contact__text">www.talmork.llc</span>
      </li>
    </ul>

    <div class="brand">
      <span class="brand__dot" aria-hidden="true"></span>
      <p class="brand__name">TALMORK</p>
      <p class="brand__since">SINCE 2026</p>
    </div>
  </section>

  <section class="card card--back" aria-label="Business card back">
    <svg class="card__frame" viewBox="0 0 582 377" aria-hidden="true">
      <defs>
        <linearGradient id="frameBack" x1="0" x2="1" y1="0" y2="0">
          <stop offset="0" stop-color="#f9f4bd" stop-opacity="1"/>
          <stop offset="0.7" stop-color="#f9f4bd" stop-opacity="1"/>
          <stop offset="0.88" stop-color="#f9f4bd" stop-opacity="0"/>
          <stop offset="1" stop-color="#f9f4bd" stop-opacity="0"/>
        </linearGradient>
      </defs>
      <rect x="33.5" y="34.5" width="515" height="308" rx="24" fill="none" stroke="url(#frameBack)" stroke-width="1"/>
    </svg>
    <h2 class="company">TALMORK BREKKESTAD</h2>
  </section>

</main>
</body>
</html>
```